Buch-/eBook-Cover für ein Fantasy Roman
Zielgruppe
Meine Zielgruppe sind Jugendliche und junge Erwachsene, aber auch für Ältere könnte mein Buch interessant sein.
Aufgabenstellung
Bei meinem Buch handelt es sich um einen Fantasy Roman. Es heißt 'Drifter - Wo die Stille wohnt' und der Autor ist Mara Wendholt.
Das Buch handelt von einem Mädchen, welches eigentlich ein ganz normales Leben führt, aber dieses durch eine Pressekonferenz vom Präsidenten komplett durcheinander gerät. Denn viele Menschen sollen an einem Virus leiden. Die Menschen sollen sich aber keine Sorgen machen. Doch alles läuft durcheinander, da die infizierten Menschen einer nach dem anderen spurlos verschwinden.
Auf meinem Cover soll keine Figur zu sehen sein. Ich hätte gerne ein Zusammenspiel zwischen den Farben Blau und Grün. sie sollen harmonisch und fließend ineinander übergehen. Auch etwas Glitzer für etwas Geheimnisvolles darf auf dem Cover sein. Den Titel hätte ich gerne in der Mitte. Wo der Autorname stehen soll, bin ich offen.

```html
<!DOCTYPE html>
<html lang="de">
<head>
<meta charset="utf-8">
<title>Drifter – Wo die Stille wohnt</title>
<link rel="stylesheet" href="https://fonts.googleapis.com/css2?family=Gloock&family=Poppins:wght@400&display=swap">
<style>
  :root {
    --page-bg: #e9e9ea;
    --deep-navy: #061a33;
    --ocean-blue: #0d3f8a;
    --teal: #1aa59a;
    --emerald: #1f9a5a;
    --mint-light: #a8f0c8;
    --title-cream: #eefbd9;
    --subtitle-white: #f4f7f2;
    --author-white: #f1f3f5;
  }
  * { margin: 0; padding: 0; box-sizing: border-box; }
  html, body {
    width: 1200px;
    height: 1200px;
    overflow: hidden;
    background: var(--page-bg);
  }
  .canvas {
    position: relative;
    width: 1200px;
    height: 1200px;
    display: flex;
    align-items: center;
    justify-content: center;
  }
  .book-cover {
    position: relative;
    width: 790px;
    height: 1090px;
    overflow: hidden;
    background: var(--deep-navy);
  }
  .cover-artwork {
    position: absolute;
    inset: 0;
    width: 100%;
    height: 100%;
  }
  .cover-text {
    position: absolute;
    inset: 0;
  }
  .book-title {
    position: absolute;
    top: 455px;
    left: 0;
    width: 100%;
    padding-left: 30px;
    text-align: center;
    font-family: "Gloock", "Bodoni Moda", serif;
    font-weight: 400;
    font-size: 128px;
    line-height: 1;
    letter-spacing: -1px;
    color: var(--title-cream);
  }
  .book-subtitle {
    position: absolute;
    top: 600px;
    left: 0;
    width: 100%;
    padding-left: 60px;
    text-align: center;
    font-family: "Gloock", "Bodoni Moda", serif;
    font-size: 30px;
    letter-spacing: 1px;
    word-spacing: 4px;
    color: var(--subtitle-white);
  }
  .book-author {
    position: absolute;
    top: 935px;
    left: 0;
    width: 100%;
    text-align: center;
    font-family: "Poppins", sans-serif;
    font-weight: 400;
    font-size: 21px;
    letter-spacing: 1px;
    text-transform: uppercase;
    color: var(--author-white);
  }
</style>
</head>
<body>
<main class="canvas">
  <section class="book-cover">
    <svg class="cover-artwork" viewBox="0 0 790 1090" preserveAspectRatio="none" role="img" aria-label="Abstrakte, fließende Farbwirbel in Grün und Blau mit feinem goldenem Glitzer">
      <defs>
        <linearGradient id="flow-base" x1="0.8" y1="0" x2="0.2" y2="1">
          <stop offset="0" stop-color="var(--emerald)"/>
          <stop offset="0.35" stop-color="var(--teal)"/>
          <stop offset="0.6" stop-color="var(--ocean-blue)"/>
          <stop offset="1" stop-color="var(--deep-navy)"/>
        </linearGradient>
        <radialGradient id="flow-glow" cx="0.6" cy="0.42" r="0.35">
          <stop offset="0" stop-color="var(--mint-light)" stop-opacity="0.75"/>
          <stop offset="1" stop-color="var(--mint-light)" stop-opacity="0"/>
        </radialGradient>
        <linearGradient id="edge-shade" x1="0" y1="0" x2="1" y2="0">
          <stop offset="0" stop-color="var(--deep-navy)" stop-opacity="0.9"/>
          <stop offset="0.25" stop-color="var(--deep-navy)" stop-opacity="0"/>
          <stop offset="0.8" stop-color="var(--deep-navy)" stop-opacity="0"/>
          <stop offset="1" stop-color="var(--deep-navy)" stop-opacity="0.85"/>
        </linearGradient>
      </defs>
      <rect width="790" height="1090" fill="url(#flow-base)"/>
      <rect width="790" height="1090" fill="url(#flow-glow)"/>
      <rect width="790" height="1090" fill="url(#edge-shade)"/>
    </svg>
    <div class="cover-text">
      <h1 class="book-title">DRIFTER</h1>
      <p class="book-subtitle">Wo die Stille wohnt</p>
      <p class="book-author">Mara Wendholt</p>
    </div>
  </section>
</main>
</body>
</html>
```